Maris Dovey Studio Business Cards

Hi - using the information and logo provided I require a two sided business card designed with the following information. The business card is a 'mini card' 3.5" x 1.25".

Front of card should be the logo attached but inverted (so the background is the peach colour and the logo white).

Back should have these details. If we can't fit the Pictogrum and Friendwall part can we just put the little logos.

Tessa Varnold

Art and Design Consultant
Dealer - Curator - Events - Styling - Creative Sourcing

P: 0438 217 604
E: tessa@marisdoveystudio.example
W: www.marisdoveystudio.example
I (pictogram image please): marisdoveystudio F (Friendwall image please): MarisDoveyAdviser

Target Market(s)

Galleries, artists, art buyers, interior design clients, event managers, creative types

Industry/Entity Type

Business

```html
<!DOCTYPE html>
<html lang="en">
<head>
<meta charset="utf-8">
<title>Maris Dovey Studio – Business Cards</title>
<link rel="stylesheet" href="https://fonts.googleapis.com/css2?family=Tinos&family=Jost:wght@400&display=swap">
<style>
  :root {
    --stage: #6f5f56;
    --card-dark: #1b1b1b;
    --card-light: #ffffff;
    --peach: #f2b89a;
    --peach-text: #f0a57c;
    --grey-name: #8a8a8a;
    --rule-dark: #4a4a4a;
    --rule-light: #d6d6d6;
    --ink: #1e1e1e;
    --white: #ffffff;
  }
  * { margin: 0; padding: 0; box-sizing: border-box; }
  html, body { width: 1200px; height: 960px; overflow: hidden; }
  body {
    background: var(--stage);
    position: relative;
    font-family: "Tinos", "Times New Roman", serif;
  }
  .card { position: absolute; width: 860px; height: 307px; }
  .card--front { left: 36px; top: 65px; background: var(--card-dark); }
  .card--back  { left: 288px; top: 475px; background: var(--card-light); }
  .abs { position: absolute; }

  /* front */
  .brand-mark { left: 176px; top: 24px; width: 100px; height: 100px; border-radius: 50%; background: var(--peach); }
  .brand-name {
    left: 30px; width: 390px; text-align: center; color: var(--grey-name);
    white-space: nowrap;
  }
  .brand-name--main { top: 142px; font-size: 29px; letter-spacing: 4px; font-family: "Tinos", serif; }
  .brand-name--sub  { top: 182px; font-size: 20px; letter-spacing: 5px; font-family: "Tinos", serif; }
  .divider { width: 3px; background: linear-gradient(#2a2a2a, #d9d9d9 50%, #2a2a2a); }
  .card--front .divider { left: 410px; top: 34px; height: 180px; }
  .person-name { left: 444px; top: 88px; font-size: 38px; color: var(--grey-name); white-space: nowrap; }
  .person-role { left: 460px; top: 134px; font-size: 22px; color: var(--peach-text); white-space: nowrap; }
  .hrule { height: 1px; }
  .card--front .hrule { left: 30px; width: 796px; background: var(--rule-dark); }
  .services {
    left: 30px; width: 796px; top: 244px; text-align: center;
    font-size: 24px; color: var(--white); white-space: nowrap;
  }

  /* back */
  .card--back .hrule { left: 28px; width: 804px; background: var(--rule-light); }
  .back-mark { left: 109px; top: 50px; width: 90px; height: 90px; border-radius: 50%; background: var(--peach); }
  .back-name { left: 28px; width: 252px; top: 160px; text-align: center; font-size: 21px; color: var(--grey-name); white-space: nowrap; }
  .card--back .divider { left: 300px; top: 43px; height: 175px; background: linear-gradient(#bcbcbc, #1e1e1e 50%, #bcbcbc); }
  .contact { left: 325px; font-size: 21.5px; color: var(--ink); white-space: nowrap; }
  .social { top: 238px; font-size: 20px; color: var(--ink); white-space: nowrap; display: flex; align-items: center; gap: 10px; }
  .social__icon { width: 28px; height: 28px; background: var(--ink); }
  .social__icon--fw { background: #3b5a98; }
  .social--pg { left: 50px; }
  .social--fw { left: 494px; }
  .social-sep { left: 440px; top: 238px; font-size: 22px; color: var(--ink); }
</style>
</head>
<body>
  <section class="card card--front" aria-label="Card front">
    <div class="abs brand-mark"></div>
    <div class="abs brand-name brand-name--main">MARIS DOVEY</div>
    <div class="abs brand-name brand-name--sub">STUDIO</div>
    <div class="abs divider"></div>
    <div class="abs person-name">Tessa Varnold</div>
    <div class="abs person-role">(Art and Design Consultant)</div>
    <div class="abs hrule" style="top:226px"></div>
    <div class="abs services">Dealer | Curator | Events | Styling | Creative Sourcing</div>
    <div class="abs hrule" style="top:280px"></div>
  </section>

  <section class="card card--back" aria-label="Card back">
    <div class="abs hrule" style="top:26px"></div>
    <div class="abs back-mark"></div>
    <div class="abs back-name">Maris Dovey Studio</div>
    <div class="abs divider"></div>
    <div class="abs contact" style="top:75px">Phone: 0438 217 604</div>
    <div class="abs contact" style="top:114px">Email: tessa@marisdoveystudio.example</div>
    <div class="abs contact" style="top:155px">Web: www.marisdoveystudio.example</div>
    <div class="abs hrule" style="top:226px"></div>
    <div class="abs social social--pg"><span class="social__icon"></span><span>Pictogrum: MarisDoveyAdviser</span></div>
    <div class="abs social-sep">|</div>
    <div class="abs social social--fw"><span class="social__icon social__icon--fw"></span><span>Friendwall: marisdoveystudio</span></div>
    <div class="abs hrule" style="top:278px"></div>
  </section>
</body>
</html>
```